Natural cosmetics company is looking for a designer to produce the labels of the products and

Hello, Nus need a label and logo design for our brand RM ORGANIC. It is a brand specializing in the sale of 100% Natural cosmetic products on the internet. The first range is based on snail slime. I am looking for a clean design in green tones. The final design must be forwarded to the supplier for printing and shipping of the products. I realized a first idea for a logo, but I am interested in other ideas / suggestions. You have carte blanche :)
Here are the rules to follow for sending labels to the supplier:
• Sizes:
- Airless bottle: 10.3 x 5.5 cm
- Jar: 20x2.5cm
• Files must be in Corel Draw (. cdr) and / or vector PDF format
You must attach the file of the fonts used for the text in the label - We need this file as many fonts are difficult to find and we might need to move some text around for printing purposes
• The logo of your brand must be in a vector format along with all other components.
• Please do not add any borders or any cut marks to the design. We will do it on our end as we need to follow specific indications with our printing suppliers.
• All text and graphics must be at least 6mm from the edge
• The dimensions indicated by us must be respected in the overall size of the label
• The resolution to be used should be 300 cpi and in CMYK
• The text size should be readable and at least 4.5 points.

```html
<!DOCTYPE html>
<html lang="en">
<head>
<meta charset="utf-8">
<title>RM Organic – Snail Slime labels</title>
<link rel="stylesheet" href="https://fonts.googleapis.com/css2?family=Mulish:wght@300;400&display=swap">
<style>
  :root {
    --ink: #1a1a1a;
    --band: #050505;
    --paper: #ffffff;
    --stage: #f2f2f2;
    --mint: #a9d8c6;
    --sage: #8fa79c;
    --orchid: #d86fd0;
  }
  * { box-sizing: border-box; margin: 0; padding: 0; }
  html, body { width: 1200px; height: 923px; overflow: hidden; }
  body {
    background: var(--stage);
    font-family: "Mulish", sans-serif;
    font-weight: 300;
    color: var(--ink);
    position: relative;
  }
  .label { position: absolute; background: var(--paper); overflow: hidden; }
  .block { position: absolute; text-align: center; }
  .artwork {
    position: absolute; top: 0; bottom: 0;
    background:
      radial-gradient(ellipse at 20% 20%, rgba(216,111,208,.55), transparent 55%),
      radial-gradient(ellipse at 75% 25%, rgba(143,167,156,.6), transparent 55%),
      radial-gradient(ellipse at 25% 80%, rgba(143,167,156,.55), transparent 55%),
      radial-gradient(ellipse at 80% 85%, rgba(216,111,208,.5), transparent 55%),
      radial-gradient(ellipse at 50% 50%, rgba(169,216,198,.6), transparent 70%);
  }
  .brand-disc {
    position: absolute; border-radius: 50%;
    background: var(--paper); border: 2px solid var(--ink);
    display: flex; align-items: center; justify-content: center;
    text-align: center; color: var(--ink); font-weight: 400;
  }
  .heading { font-weight: 400; }
  .icons { position: absolute; display: flex; flex-direction: column; align-items: center; }
  .icon { border: 2px solid var(--ink); }
  .icon.round { border-radius: 50%; }
  .vertical {
    position: absolute; writing-mode: vertical-rl; transform: rotate(180deg);
    font-size: 9px; line-height: 1.1; text-align: left;
  }

  /* jar strip */
  .jar { left: 61px; top: 74px; width: 1072px; height: 104px;
    border-top: 3px solid var(--band); border-bottom: 3px solid var(--band); }
  .jar .block { font-size: 11px; line-height: 13.4px; letter-spacing: -0.15px; }
  .jar .intro { left: 2px; top: 2px; width: 270px; }
  .jar .artwork { left: 274px; width: 353px; }
  .jar .brand-disc { left: 364px; top: 5px; width: 88px; height: 88px; font-size: 12px; }
  .jar .product { position: absolute; left: 464px; top: 40px; font-size: 16px; }
  .jar .volume { position: absolute; left: 464px; top: 84px; font-size: 9px; }
  .jar .directions { left: 627px; top: 5px; width: 199px; }
  .jar .ingredients { left: 832px; top: 5px; width: 182px; }
  .jar .icons { left: 1016px; top: 4px; gap: 8px; }
  .jar .vertical { left: 1040px; top: 6px; height: 90px; }

  /* airless bottle label */
  .bottle { left: 174px; top: 404px; width: 852px; height: 431px; }
  .bottle .band { position: absolute; left: 0; right: 0; height: 33px; background: var(--band); }
  .bottle .band.top { top: 0; }
  .bottle .band.bottom { bottom: 0; color: var(--paper); font-size: 15px;
    display: flex; align-items: center; justify-content: center; font-weight: 400; }
  .bottle .artwork { left: 160px; width: 515px; top: 33px; bottom: 33px; }
  .bottle .intro { left: 0; top: 43px; width: 174px; font-size: 17px; line-height: 19.4px; }
  .bottle .brand-disc { left: 353px; top: 151px; width: 144px; height: 144px; font-size: 19px; }
  .bottle .product { position: absolute; left: 0; width: 850px; text-align: center; top: 370px; font-size: 24px; }
  .bottle .facts { left: 660px; top: 43px; width: 152px; font-size: 14px; line-height: 16.8px; }
  .bottle .facts .heading { font-size: 15px; }
  .bottle .facts .gap { margin-top: 12px; }
  .bottle .icons { left: 814px; top: 48px; gap: 18px; }
  .bottle .vertical { left: 818px; top: 310px; height: 88px; font-size: 10px; }
</style>
</head>
<body>

<section class="label jar" aria-label="Jar label">
  <div class="block intro">
    <p>RM ORGANIC Snail Slime</p>
    <p>Lorem ipsum dolor sit amet. Dolor dolores kasd sed ipsum elitr amet ut. Et eirmod at stet. Ipsum est gubergren. Quis dolor amet qui sadipscing suscipit dolor. Aliquip wisi vel invidunt accusam augue. Nihil elitr autem. Consectetuer vero elitr. Praesent vero delenit</p>
  </div>
  <div class="artwork" role="img" aria-label="Painted brush strokes in pink, sage and mint"></div>
  <div class="brand-disc">RM<br>Organic</div>
  <p class="product">Snail Slime</p>
  <p class="volume">℮30ml/1.01 fl.oz.</p>
  <div class="block directions">
    <p class="heading">DIRECTIONS:</p>
    <p>Quis dolor amet qui sadipscing suscipit dolor. Aliquip wisi vel invidunt accusam augue. Nihil elitr autem. Consectetuer vero elitr. Praesent vero delenit sed ex</p>
  </div>
  <div class="block ingredients">
    <p class="heading">INGREDIENTS:</p>
    <p>Water,Butylene Glycol, Tetrapeptide,Palmitoyl Tripeptide,Collagen Amino Acids,Dexpanthenol,Sodium Hyaluronate,Phenoxyethanol</p>
  </div>
  <div class="icons" aria-hidden="true">
    <span class="icon round" style="width:14px;height:14px"></span>
    <span class="icon round" style="width:18px;height:18px"></span>
    <span class="icon round" style="width:18px;height:18px"></span>
    <span class="icon" style="width:14px;height:16px"></span>
  </div>
  <p class="vertical">RM Organic,<br>Adress,adress,adress<br>MADE IN CHINA</p>
</section>

<section class="label bottle" aria-label="Airless bottle label">
  <div class="band top"></div>
  <div class="artwork" role="img" aria-label="Painted brush strokes in pink, sage and mint"></div>
  <div class="block intro">
    <p>RM ORGANIC<br>Snail Slim<br>Lorem ipsum dolor<br>sit amet. Dolor<br>dolores kasd sed<br>ipsum elitr amet ut.<br>Et eirmod at stet.<br>Ipsum est<br>gubergren. Quis<br>dolor amet qui<br>sadipscing suscipit<br>dolor. Aliquip wisi<br>vel invidunt<br>accusam augue.<br>Nihil elitr autem.<br>Consectetuer vero<br>elitr. Praesent vero<br>delenit sed ex</p>
  </div>
  <div class="brand-disc">RM<br>Organic</div>
  <p class="product">Snail Slime</p>
  <div class="block facts">
    <p class="heading">INGREDIENTS:</p>
    <p>Water,<br>Butylene Glycol,<br>Tetrapeptide,<br>Palmitoyl Tripeptide,<br>Collagen Amino<br>Acids,Dexpanthenol,<br>Sodium Hyaluronate,<br>Phenoxyethanol,<br>Ethylhexylglycerin</p>
    <p class="heading gap">DIRECTIONS:</p>
    <p>Quis dolor amet qui<br>sadipscing suscipit<br>dolor. Aliquip wisi<br>vel invidunt accusam<br>augue. Nihil elitr<br>autem.<br>Consectetuer vero<br>elitr. Praesent vero<br>delenit sed ex</p>
  </div>
  <div class="icons" aria-hidden="true">
    <span class="icon round" style="width:20px;height:20px"></span>
    <span class="icon round" style="width:30px;height:30px"></span>
    <span class="icon round" style="width:30px;height:30px"></span>
    <span class="icon" style="width:24px;height:30px"></span>
  </div>
  <p class="vertical">RM Organic,<br>Adress,adress,adress<br>MADE IN CHINA</p>
  <div class="band bottom">℮30ml/1.01 fl.oz.</div>
</section>

</body>
</html>
```